Travel Agency Website - Simple General

Need a 7 page simple design that is pretty repetitive. Need to be able to load quickly that is SEO optimized. Trying to give ideas on what they can do, be personal as we are local, but at the same time come across as professional and get information easily with little burden.

- Landing Page
- Brimwell Vacations Page
- Family Trips
- Road Trips from Texas
- Other Destinations
- About Us Page
- Contact Us Page

Target Market(s)

Families

Coding

Coded - Design and coding required

Number of Pages Required

5+ page

Colors

Designer to choose colors to be used in the design.

Requirements
Must have
• Like it to flow easily with our logo. Use that for colors, etc.

```html
<!DOCTYPE html>
<html lang="en">
<head>
<meta charset="utf-8">
<title>Hum Along Travel Co. — Plan Your Perfect Trip</title>
<link href="https://fonts.googleapis.com/css2?family=Outfit:wght@400;500;700;800&display=swap" rel="stylesheet">
<style>
:root{
  --teal:#1c5a60;
  --gold:#c8973f;
  --gold-light:#d9ad5e;
  --cream:#f8f4ec;
  --white:#ffffff;
  --ink:#2a2a2a;
}
*{margin:0;padding:0;box-sizing:border-box}
html,body{width:1200px;height:1017px;overflow:hidden}
body{background:var(--cream);font-family:'Outfit',sans-serif;color:var(--teal);position:relative}
.contact-bar{position:absolute;left:573px;top:0;width:554px;height:42px;background:var(--teal);border-radius:0 0 12px 12px;display:flex;align-items:center;justify-content:center;gap:22px;color:var(--white);font-size:14px}
.contact-bar span{display:flex;align-items:center;gap:8px}
.contact-bar .dot{width:20px;height:20px;border-radius:50%;background:var(--white);display:flex;align-items:center;justify-content:center}
.brand{position:absolute;left:82px;top:58px;display:flex;align-items:center;gap:10px}
.brand .mark{width:42px;height:42px;border-radius:50%;background:var(--teal)}
.brand .name{font-size:21px;font-weight:700;color:var(--teal);line-height:1.05;width:130px}
.nav{position:absolute;left:0;top:85px;width:1200px;height:22px;font-size:15px;color:var(--teal)}
.nav > *{position:absolute;top:0;line-height:22px;white-space:nowrap}
.nav .home{left:304px;top:4px}
.nav .n1{left:342px}
.nav .n2{left:485px}
.nav .n3{left:590px}
.nav .n4{left:730px}
.nav .n5{left:899px}
.btn-contact{position:absolute;left:980px;top:76px;width:144px;height:38px;border-radius:19px;background:var(--gold);color:var(--white);font-size:15px;display:flex;align-items:center;padding-left:27px}
.btn-contact .arrow{position:absolute;right:7px;top:5px;background:var(--gold-light)}
.eyebrow{position:absolute;left:0;width:1224px;top:170px;text-align:center;font-size:26px;font-weight:400;letter-spacing:.5px}
.title{position:absolute;left:0;width:1216px;top:208px;text-align:center;font-size:49px;font-weight:800;letter-spacing:1px}
.grid{position:absolute;left:85px;top:315px;display:grid;grid-template-columns:510px 510px;grid-auto-rows:279px;gap:11px 9px}
.card{position:relative;border-radius:6px;overflow:hidden;display:block}
.card .label{position:absolute;left:42px;bottom:22px;color:var(--white);font-weight:700;font-size:20px;line-height:1.1;text-transform:uppercase}
.card .label small{display:block;text-transform:none;font-size:13px;margin-top:4px}
.card .arrow{position:absolute;right:16px;bottom:16px}
.arrow{width:28px;height:28px;border-radius:50%;background:var(--gold);display:flex;align-items:center;justify-content:center}
.photo-park{background:linear-gradient(180deg,#2c6fd4 0%,#4a85c9 45%,#3d5a3a 75%,#474b4f 100%)}
.photo-canyon{background:linear-gradient(180deg,#5c9ad8 0%,#b7cde0 30%,#c8602a 55%,#4d6b34 75%,#7a6a55 100%)}
.photo-lake{background:linear-gradient(180deg,#bcd0e6 0%,#e8eef2 25%,#7f9a5c 42%,#5e86a4 65%,#7c7b6f 100%)}
.photo-coast{background:linear-gradient(180deg,#2fb3b5 0%,#2aa0a6 40%,#8d7562 70%,#6a5a4e 100%)}
.footer{position:absolute;left:0;top:935px;width:1200px;height:82px;background:var(--white)}
.footer p{position:absolute;left:0;width:1160px;top:31px;text-align:center;font-size:15px;color:var(--ink);letter-spacing:.3px}
.social{position:absolute;left:1024px;top:24px;display:flex;gap:8px}
.social span{width:24px;height:24px;border-radius:50%;background:var(--teal)}
</style>
</head>
<body>
<div class="contact-bar">
  <span><i class="dot"><svg width="11" height="9" viewBox="0 0 11 9"><rect x=".5" y=".5" width="10" height="8" fill="none" stroke="#1c5a60"/><path d="M.5 .5l5 4 5-4" fill="none" stroke="#1c5a60"/></svg></i>hello@humalongtravel.com</span>
  <span><i class="dot"><svg width="11" height="11" viewBox="0 0 24 24"><path fill="#1c5a60" d="M6.6 10.8a15 15 0 0 0 6.6 6.6l2.2-2.2c.3-.3.7-.4 1-.2 1.1.4 2.3.6 3.6.6.6 0 1 .4 1 1V20c0 .6-.4 1-1 1A17 17 0 0 1 3 4c0-.6.4-1 1-1h3.5c.6 0 1 .4 1 1 0 1.3.2 2.5.6 3.6.1.3 0 .7-.2 1z"/></svg></i>Phone Number (555) 014 2290</span>
</div>

<div class="brand"><span class="mark"></span><span class="name">Hum Along Travel Co.</span></div>

<nav class="nav">
  <svg class="home" width="14" height="13" viewBox="0 0 14 13"><path d="M7 0L0 6h2v7h4V9h2v4h4V6h2z" fill="#c8973f"/></svg>
  <span class="n1">Brimwell Vacations</span>
  <span class="n2">Family Trips</span>
  <span class="n3">Texas Road Trips</span>
  <span class="n4">Other Destinations</span>
  <span class="n5">About Us</span>
</nav>
<div class="btn-contact">Contact Us<span class="arrow"><svg width="10" height="10" viewBox="0 0 10 10"><path d="M2 8L8 2M3 2h5v5" stroke="#fff" stroke-width="1.4" fill="none"/></svg></span></div>

<h2 class="eyebrow">HUM ALONG TRAVEL CO.</h2>
<h1 class="title">PLAN YOUR PERFECT TRIP</h1>

<main class="grid">
  <a class="card photo-park" role="img" aria-label="Theme park entrance arch with palm trees under a blue sky">
    <span class="label">Brimwell Vacations<br>Land &amp; Sea</span>
    <span class="arrow"><svg width="10" height="10" viewBox="0 0 10 10"><path d="M2 8L8 2M3 2h5v5" stroke="#fff" stroke-width="1.4" fill="none"/></svg></span>
  </a>
  <a class="card photo-canyon" role="img" aria-label="Red rock canyon with a winding road through green brush">
    <span class="label">Texas Road Trips<small>(Partnership with Piney Ridge Van Rentals)</small></span>
    <span class="arrow"><svg width="10" height="10" viewBox="0 0 10 10"><path d="M2 8L8 2M3 2h5v5" stroke="#fff" stroke-width="1.4" fill="none"/></svg></span>
  </a>
  <a class="card photo-lake" role="img" aria-label="Family resting by a mountain lake with snowy peaks">
    <span class="label">Family Trips</span>
    <span class="arrow"><svg width="10" height="10" viewBox="0 0 10 10"><path d="M2 8L8 2M3 2h5v5" stroke="#fff" stroke-width="1.4" fill="none"/></svg></span>
  </a>
  <a class="card photo-coast" role="img" aria-label="Hiker walking down stone steps toward a turquoise sea cove">
    <span class="label">Other Destinations</span>
    <span class="arrow"><svg width="10" height="10" viewBox="0 0 10 10"><path d="M2 8L8 2M3 2h5v5" stroke="#fff" stroke-width="1.4" fill="none"/></svg></span>
  </a>
</main>

<footer class="footer">
  <p>© 2026 Hum Along Travel Co. All Right Reserved</p>
  <div class="social"><span></span><span></span></div>
</footer>
</body>
</html>
```